Looking for a modern, Professional business card design

We have a simple business card, but are looking for a more modern, professional look. A sample of the basic card is attached as well as the logo. We would also like to add that we offer:
Struggling with your finances?
- Learn to become debt free
- Discover the power of cash
- Control your money instead of it controlling you
Let us help you achieve a new level of financial freedom!
Also, we would like to have a "SPECIAL OFFER!: FREE 30 minute consultation"
Financial Planning

```html
<!DOCTYPE html>
<html lang="en">
<head>
<meta charset="utf-8">
<title>Harbor Money Coaching – Business Card</title>
<link href="https://fonts.googleapis.com/css2?family=Roboto:wght@400;500;700;900&family=Archivo+Black&family=Oswald:wght@500&display=swap" rel="stylesheet">
<style>
  :root {
    --backdrop: #d9d6d1;
    --card: #eeeeec;
    --card-edge: #c9c9c6;
    --green: #2e8b2e;
    --green-dark: #1f6a1f;
    --band: #1b1c1c;
    --band-light: #343535;
    --ink: #2a2a2a;
    --muted: #e6e6e6;
  }
  * { margin: 0; padding: 0; box-sizing: border-box; }
  html, body {
    width: 1200px; height: 969px; overflow: hidden;
    background: var(--backdrop);
  }
  .canvas {
    position: relative; width: 1200px; height: 969px;
    display: flex; align-items: center; justify-content: center;
  }
  .card {
    position: relative; width: 440px; height: 776px;
    background: var(--card);
    border: 1px solid var(--card-edge);
    border-radius: 22px;
    overflow: hidden;
    font-family: "Roboto", Arial, sans-serif;
    color: var(--ink);
    box-shadow: 0 10px 30px rgba(0,0,0,0.12);
  }
  .brand {
    position: absolute; top: 52px; left: 30px; right: 20px;
  }
  .brand-name {
    display: flex; align-items: center; gap: 14px;
    font-weight: 700; font-size: 40px; line-height: 1.05;
    color: var(--green-dark); letter-spacing: 0.5px;
  }
  .brand-dot {
    width: 46px; height: 46px; border-radius: 50%;
    background: var(--green); flex: none;
  }
  .brand-tagline {
    margin-top: 12px; margin-left: 60px;
    font-size: 13px; color: #444; font-style: italic;
  }
  .name-band {
    position: absolute; top: 227px; left: 0; right: 0; height: 114px;
    background: linear-gradient(180deg, var(--band-light), var(--band));
    border-top: 4px solid var(--green);
    border-bottom: 4px solid var(--green);
    padding: 22px 32px 0;
  }
  .person-name {
    font-size: 30px; font-weight: 500; letter-spacing: 1.5px;
    color: var(--green);
  }
  .person-title {
    margin-top: 8px; font-size: 20px; color: var(--muted);
  }
  .contacts {
    position: absolute; top: 360px; left: 32px; list-style: none;
  }
  .contacts li {
    display: flex; align-items: center; gap: 14px;
    height: 30px; font-size: 20px;
  }
  .contacts svg { width: 20px; height: 20px; fill: var(--green); flex: none; }
  .pitch {
    position: absolute; top: 472px; left: 32px; right: 24px;
  }
  .pitch-heading {
    font-size: 21px; font-weight: 700; color: var(--green-dark);
    letter-spacing: 0.5px;
  }
  .benefits { list-style: none; margin-top: 10px; }
  .benefits li {
    position: relative; padding-left: 20px;
    font-size: 16.5px; line-height: 31px;
  }
  .benefits li::before {
    content: ""; position: absolute; left: 3px; top: 13px;
    width: 7px; height: 7px; border-radius: 50%; background: var(--green);
  }
  .pitch-closing {
    margin-top: 16px;
    font-family: "Oswald", "Arial Narrow", sans-serif;
    font-size: 15px; color: #222; letter-spacing: 0.2px;
  }
  .offer {
    position: absolute; top: 664px; left: 32px;
  }
  .offer-title {
    font-family: "Archivo Black", "Arial Black", sans-serif;
    font-size: 40px; color: var(--green-dark); letter-spacing: 1px;
    line-height: 1;
  }
  .offer-detail {
    margin-top: 10px;
    font-family: "Archivo Black", "Arial Black", sans-serif;
    font-size: 21px; letter-spacing: 0.5px; color: #111;
  }
  .offer-detail .highlight { color: var(--green-dark); }
</style>
</head>
<body>
<main class="canvas">
  <article class="card">
    <header class="brand">
      <div class="brand-name"><span class="brand-dot"></span>Harbor Money<br>Coaching</div>
      <p class="brand-tagline">Achieve a new level of personal freedom</p>
    </header>

    <section class="name-band">
      <h1 class="person-name">DANIEL R. HAYES</h1>
      <p class="person-title">Personal Financial Coach</p>
    </section>

    <ul class="contacts">
      <li>
        <svg viewBox="0 0 20 20" aria-hidden="true"><path d="M6 1h8a2 2 0 0 1 2 2v14a2 2 0 0 1-2 2H6a2 2 0 0 1-2-2V3a2 2 0 0 1 2-2zm0 3v10h8V4H6zm4 11.5a1 1 0 1 0 0 2 1 1 0 0 0 0-2z"/></svg>
        (555) 014-2290
      </li>
      <li>
        <svg viewBox="0 0 20 20" aria-hidden="true"><path d="M2 4h16v12H2V4zm1.5 1.5v.4L10 10.5l6.5-4.6v-.4h-13zm0 2.2v6.8h13V7.7L10 12.3 3.5 7.7z"/></svg>
        daniel@steadymoneycoach.com
      </li>
      <li>
        <svg viewBox="0 0 20 20" aria-hidden="true"><path d="M10 1a9 9 0 1 0 0 18 9 9 0 0 0 0-18zm5.8 5h-2.6a13 13 0 0 0-1.3-3.3A7.1 7.1 0 0 1 15.8 6zM10 3c.8 1 1.4 2 1.8 3H8.2c.4-1 1-2 1.8-3zM3.3 12a7 7 0 0 1 0-4h3a15 15 0 0 0 0 4h-3zm.9 2h2.6c.3 1.2.8 2.3 1.3 3.3A7.1 7.1 0 0 1 4.2 14zm2.6-8H4.2a7.1 7.1 0 0 1 3.9-3.3C7.6 3.7 7.1 4.8 6.8 6zM10 17c-.8-1-1.4-2-1.8-3h3.6c-.4 1-1 2-1.8 3zm2.1-5H7.9a13 13 0 0 1 0-4h4.2a13 13 0 0 1 0 4zm-.2 5.3c.5-1 1-2.1 1.3-3.3h2.6a7.1 7.1 0 0 1-3.9 3.3zM13.7 12a15 15 0 0 0 0-4h3a7 7 0 0 1 0 4h-3z"/></svg>
        www.steadymoneycoach.com
      </li>
    </ul>

    <section class="pitch">
      <h2 class="pitch-heading">STRUGGLING WITH YOUR FINANCES?</h2>
      <ul class="benefits">
        <li>Learn to become debt free</li>
        <li>Discover the power of cash</li>
        <li>Control your money instead of it controlling you</li>
      </ul>
      <p class="pitch-closing">LET US HELP YOU ACHIEVE A NEW LEVEL OF FINANCIAL FREEDOM!</p>
    </section>

    <section class="offer">
      <p class="offer-title">SPECIAL OFFER!</p>
      <p class="offer-detail">FREE <span class="highlight">30 MINUTE CONSULTATION</span></p>
    </section>
  </article>
</main>
</body>
</html>
```